8x8 Social Media Ad - Brant Summit Expo

Attention Real Estate Agents
Please join us for our
Quarterly Real Estate Training Expo
The 2nd Saturday of February, May, August and November
Our Next Training Expo is _________________________________
From 9 am to 1 pm
at
Halvorne Suites Millbrook Court
4817 Copper Willow Lane, Dunmere, MD 20588
Scheduled Speakers
9:00 am - Marcus Pellington - Orientation
9:30 am - Derrin Oakfield - Multiple Income Streams / Crest Program
10:00 am - Talia Brennick - Marketing though Social Media
10:45 am - Rex Dunmore - Generating Business through Ru-Plaza
11:30 am - Kemi Adeyoro - Real Estate Investing
12:15 pm - Gregor Tamsey - (Main Speaker) Training Topic TBA
For more information call Marcus Pellington at (240) 555-0183 or email mpellington@brantsummithomes.example

```html
<!DOCTYPE html>
<html lang="en">
<head>
<meta charset="utf-8">
<title>Brant Summit Expo – Quarterly Real Estate Training Expo</title>
<link rel="stylesheet" href="https://fonts.googleapis.com/css2?family=Bebas+Neue&family=Poppins:wght@400;600;700;800&display=swap">
<style>
  :root {
    --teal: #0a8a99;
    --teal-bright: #13a3b3;
    --teal-deep: #0b5e66;
    --ink: #111111;
    --black: #000000;
    --white: #ffffff;
    --grey-bar: #d2d1ce;
    --city-top: #4a4a4a;
    --city-bottom: #1f1f1f;
    --portrait-a: #b8b2a8;
    --portrait-b: #5b5550;
  }
  * { margin: 0; padding: 0; box-sizing: border-box; }
  html, body { width: 1153px; height: 1200px; overflow: hidden; background: var(--white); }
  body { position: relative; font-family: "Poppins", sans-serif; color: var(--ink); }

  .ad { position: absolute; left: 159px; top: 186px; width: 834px; height: 834px; background: var(--white); overflow: hidden; }
  .abs { position: absolute; white-space: nowrap; }

  /* brand */
  .brand { left: 31px; top: 40px; width: 168px; display: flex; align-items: center; gap: 8px; }
  .brand-mark { width: 18px; height: 18px; background: var(--teal); flex: none; }
  .brand-name { font-weight: 800; font-size: 25px; color: var(--teal); letter-spacing: .5px; line-height: 1.05; }

  .attention { left: 207px; top: 36px; font-weight: 800; font-size: 38px; line-height: 1; letter-spacing: 1px; }
  .audience { left: 207px; top: 78px; font-weight: 700; font-size: 22.5px; line-height: 1; color: var(--teal); letter-spacing: .6px; }

  .invite { left: 35px; top: 136px; width: 380px; height: 36px; background: var(--black); color: var(--white); border-radius: 3px;
            font-weight: 600; font-size: 21px; letter-spacing: 2.6px; line-height: 36px; padding-left: 10px; }
  .quarterly { left: 34px; top: 170px; font-weight: 700; font-size: 51px; line-height: 1.1; color: var(--teal); letter-spacing: 1px; }
  .headline { font-family: "Bebas Neue", sans-serif; line-height: 1; }
  .headline-1 { left: 33px; top: 224px; font-size: 96px; color: var(--ink); letter-spacing: -.5px; }
  .headline-2 { left: 31px; top: 301px; font-size: 96px; color: var(--teal); letter-spacing: -.5px; }

  .schedule-tag { left: 35px; top: 394px; width: 246px; height: 34px; background: var(--black); border: 2px solid var(--teal);
                  border-radius: 3px; color: var(--white); font-weight: 700; font-size: 18px; line-height: 30px; padding-left: 13px; }
  .schedule-tag sup { font-size: 10px; }
  .months { left: 35px; top: 432px; font-weight: 700; font-size: 20px; line-height: 23px; }
  .divider { left: 305px; top: 403px; width: 3px; height: 70px; background: var(--grey-bar); }
  .hours-label { left: 323px; top: 406px; font-family: "Bebas Neue", sans-serif; font-size: 41px; line-height: 1; }
  .hours { left: 323px; top: 439px; font-family: "Bebas Neue", sans-serif; font-size: 42px; line-height: 1; color: var(--teal); }

  .next { left: 36px; top: 485px; font-weight: 700; font-size: 21px; line-height: 1.2; }
  .next-date { left: 34px; top: 514px; width: 434px; height: 27px; background: var(--grey-bar); border-radius: 3px; }

  .venue { left: 35px; top: 558px; display: flex; gap: 10px; }
  .venue svg { width: 18px; height: 22px; margin-top: 1px; }
  .venue-text { font-size: 17px; line-height: 21px; }

  .skyline { left: 0; top: 598px; width: 527px; height: 236px;
             background: linear-gradient(180deg, rgba(74,74,74,0) 0%, var(--city-top) 22%, var(--city-bottom) 100%); }

  .contact-lead { left: 34px; top: 755px; font-weight: 700; font-size: 17.5px; color: var(--teal); }
  .contact-line { left: 35px; top: 783px; width: 484px; display: flex; align-items: center; gap: 7px; color: var(--white); font-weight: 700; font-size: 13.5px; }
  .contact-line svg { width: 16px; height: 16px; flex: none; }
  .contact-line .email { margin-left: 16px; }

  /* speakers */
  .speakers-panel { left: 527px; top: 0; width: 307px; height: 651px; background: var(--black); }
  .main-panel { left: 527px; top: 651px; width: 307px; height: 183px; background: var(--teal-deep); }
  .speakers-tab { left: 517px; top: 32px; width: 236px; height: 50px; }
  .speakers-tab span { position: absolute; left: 21px; top: 13px; color: var(--white); font-weight: 700; font-size: 17px; letter-spacing: .3px; }

  .portrait { position: absolute; border-radius: 50%; border: 3px solid var(--teal); box-shadow: inset 0 0 0 3px var(--white);
              background: linear-gradient(180deg, var(--portrait-a) 0%, var(--portrait-b) 100%); }
  .slot { position: absolute; left: 604px; color: var(--white); }
  .slot .time { font-weight: 800; font-size: 26px; line-height: 1; }
  .slot .name { font-weight: 800; font-size: 19.5px; line-height: 1.15; color: var(--teal-bright); margin-top: 2px; }
  .slot .topic { font-size: 15px; line-height: 16px; }
  .slot.main { left: 607px; }
  .slot.main .time { font-size: 30px; }
  .slot.main .name { font-size: 22px; color: var(--teal-bright); }
  .slot.main .role { font-weight: 600; font-size: 20px; line-height: 1.2; }
  .slot.main .topic { font-size: 16px; margin-top: 4px; }
</style>
</head>
<body>
<main class="ad">
  <div class="abs skyline" role="img" aria-label="City skyline silhouette in dark greys"></div>

  <div class="abs brand"><span class="brand-mark"></span><span class="brand-name">BRANT<br>SUMMIT</span></div>
  <h1 class="abs attention">ATTENTION!!</h1>
  <p class="abs audience">REAL ESTATE AGENTS</p>

  <p class="abs invite">PLEASE JOIN US FOR OUR</p>
  <p class="abs quarterly">QUARTERLY</p>
  <p class="abs headline headline-1">REAL ESTATE</p>
  <p class="abs headline headline-2">TRAINING EXPO</p>

  <p class="abs schedule-tag">THE 2<sup>nd</sup> SATURDAY OF</p>
  <p class="abs months">FEBRUARY, MAY,<br>AUGUST &amp; NOVEMBER</p>
  <div class="abs divider"></div>
  <p class="abs hours-label">FROM</p>
  <p class="abs hours">9 AM - 1 PM</p>

  <p class="abs next">Our Next Training Expo is</p>
  <div class="abs next-date"></div>

  <div class="abs venue">
    <svg viewBox="0 0 18 22" aria-hidden="true"><path d="M9 1a7 7 0 0 0-7 7c0 5 7 11 7 11s7-6 7-11a7 7 0 0 0-7-7z" fill="none" stroke="var(--teal)" stroke-width="2.4"/><circle cx="9" cy="8" r="2.6" fill="var(--teal)"/><path d="M2 21h14" stroke="var(--teal)" stroke-width="2"/></svg>
    <p class="venue-text">Halvorne Suites Millbrook Court<br>4817 Copper Willow Lane, Dunmere, MD 20588</p>
  </div>

  <p class="abs contact-lead">For more information call Marcus Pellington</p>
  <p class="abs contact-line">
    <svg viewBox="0 0 24 24" aria-hidden="true"><path d="M6.6 10.8a15 15 0 0 0 6.6 6.6l2.2-2.2c.3-.3.7-.4 1-.2 1.1.4 2.3.6 3.6.6.6 0 1 .4 1 1V20c0 .6-.4 1-1 1A17 17 0 0 1 3 4c0-.6.4-1 1-1h3.5c.6 0 1 .4 1 1 0 1.3.2 2.5.6 3.6.1.3 0 .7-.2 1z" fill="var(--teal)"/></svg>
    <span>(240) 555-0183</span>
    <svg class="email" viewBox="0 0 24 24" aria-hidden="true"><rect x="2" y="5" width="20" height="14" rx="1.5" fill="none" stroke="var(--teal)" stroke-width="2"/><path d="M2.5 6l9.5 7 9.5-7" fill="none" stroke="var(--teal)" stroke-width="2"/></svg>
    <span>mpellington@brantsummithomes.example</span>
  </p>

  <div class="abs speakers-panel"></div>
  <div class="abs main-panel"></div>
  <div class="abs speakers-tab">
    <svg width="236" height="50" viewBox="0 0 236 50" aria-hidden="true"><path d="M8 0H222L236 24 222 48H8C3 48 0 45 0 40V8C0 3 3 0 8 0Z" fill="var(--teal)"/></svg>
    <span>SCHEDULED SPEAKERS</span>
  </div>

  <div class="portrait" role="img" aria-label="Portrait photo of Marcus Pellington" style="left:483px;top:92px;width:100px;height:100px"></div>
  <div class="slot" style="top:113px"><p class="time">9:00 AM</p><p class="name">MARCUS PELLINGTON</p><p class="topic">Orientation</p></div>

  <div class="portrait" role="img" aria-label="Portrait photo of Derrin Oakfield" style="left:483px;top:200px;width:100px;height:100px"></div>
  <div class="slot" style="top:209px"><p class="time">9:30 AM</p><p class="name">DERRIN OAKFIELD</p><p class="topic">Multiple Income Streams /<br>Crest Program</p></div>

  <div class="portrait" role="img" aria-label="Portrait photo of Talia Brennick" style="left:483px;top:310px;width:100px;height:100px"></div>
  <div class="slot" style="top:322px"><p class="time">10:00 AM</p><p class="name">TALIA BRENNICK</p><p class="topic">Marketing though<br>Social Media</p></div>

  <div class="portrait" role="img" aria-label="Portrait photo of Rex Dunmore" style="left:483px;top:423px;width:100px;height:100px"></div>
  <div class="slot" style="top:434px"><p class="time">10:45 AM</p><p class="name">REX DUNMORE</p><p class="topic">Generating Business<br>through Ru-Plaza</p></div>

  <div class="portrait" role="img" aria-label="Portrait photo of Kemi Adeyoro" style="left:483px;top:536px;width:101px;height:101px"></div>
  <div class="slot" style="top:554px"><p class="time">11:30 AM</p><p class="name">KEMI ADEYORO</p><p class="topic">Real Estate Investing</p></div>

  <div class="portrait" role="img" aria-label="Portrait photo of main speaker Gregor Tamsey" style="left:485px;top:670px;width:107px;height:107px"></div>
  <div class="slot main" style="top:686px"><p class="time">12:15 PM</p><p class="name">GREGOR TAMSEY</p><p class="role">(Main Speaker)</p><p class="topic">Training Topic TBA</p></div>
</main>
</body>
</html>
```